Ledgerwise Forge - WordPress Theme & Logo

Design a logo and Wordpress website design for Ledgerwise Forge. Ledgerwise Forge provides cryptocurrency development services to clients who need a team to create & continue developing a new cryptocurrency or who want to replace their current cryptocurrency development team. more details in the attached document.
Updates

Target Market(s)

Entrepreneurs who are building a business / platform that makes use of an underlying cryptocurrency.

Logo Text

LF or Ledgerwise Forge

Coding

Coded - Design and coding required

Font styles to use
Sans Serif

Requirements
Must have
• Professional logo, complete coded Wordpress theme for all pages, containing all specified links and buttons
Nice to have
• It would be nice if the buttons that are meant to integrate with Dealtrail contain the necessary code for that. I can provide any necessary Dealtrail details from my account.
Should not have
• Slow loading time

```html
<!DOCTYPE html>
<html lang="en">
<head>
<meta charset="utf-8">
<title>Ledgerwise Forge</title>
<link rel="stylesheet" href="https://fonts.googleapis.com/css2?family=Roboto:ital,wght@0,400;0,500;0,700;1,400&family=Rubik:wght@500;600&display=swap">
<style>
:root{
  --brand:#22aedc;
  --brand-light:#8fdcf5;
  --ink:#111418;
  --muted:#8a8f96;
  --line:#d9dde1;
  --band:#e9f5f8;
  --band-edge:#cfe9f0;
  --white:#ffffff;
}
*{box-sizing:border-box;margin:0;padding:0}
html,body{width:1200px;height:3603px;overflow:hidden;background:var(--white)}
body{position:relative;font-family:'Roboto',sans-serif;color:var(--ink)}
.abs{position:absolute}
h1,h2{font-family:'Rubik',sans-serif;font-weight:600;color:var(--ink)}
.btn{position:absolute;display:flex;align-items:center;justify-content:center;border:2px solid var(--brand);border-radius:3px;color:var(--brand);font-weight:700;font-size:14px;text-decoration:none;background:var(--white)}
.rule{position:absolute;height:2px;width:50px;background:var(--brand-light)}
.centered{left:0;width:1200px;text-align:center}

/* header */
.brand-mark{position:absolute;display:flex;align-items:center;gap:10px}
.brand-dot{width:14px;height:14px;border-radius:50%;background:var(--brand)}
.brand-name{font-family:'Roboto',sans-serif;font-weight:500;font-size:20px;color:var(--ink);white-space:nowrap}
.main-nav{position:absolute;left:405px;top:37px;display:flex;gap:25px;font-size:12px}
.main-nav a{color:var(--ink);text-decoration:none}
.main-nav a.active{border-bottom:2px solid var(--brand);padding-bottom:9px}

/* side section index */
.side-index{position:absolute;left:1110px;width:64px;text-align:center;font-size:9px;font-weight:500}
.side-index::before{content:"";display:block;width:1px;height:40px;background:var(--line);margin:0 auto 8px}

/* hero */
.hero-title{font-size:40px;line-height:50px}
.hero-text{font-size:13px;line-height:25px;color:var(--muted)}

/* hex cards */
.hex-card{position:absolute;width:300px;height:342px;text-align:center}
.hex-card svg{position:absolute;inset:0}
.hex-card .label{position:absolute;left:0;right:0;top:162px;font-size:18px;font-weight:500}
.hex-card .desc{position:absolute;left:65px;right:65px;top:200px;font-size:13px;line-height:22px;color:var(--muted)}
.hex-card.featured .label,.hex-card.featured .desc{color:var(--white)}
.hex-card .icon{position:absolute;left:115px;top:75px}

/* about */
.about-text{font-size:13px;line-height:22.5px;color:var(--muted);width:340px}

/* testimonials */
.quote-card{position:absolute;top:2236px;height:180px;background:var(--white);border:1px solid #e3e6e9;box-shadow:0 2px 8px rgba(0,0,0,.12);text-align:center}
.quote-card::after{content:"";position:absolute;left:50%;bottom:-9px;width:16px;height:16px;margin-left:-8px;background:var(--white);transform:rotate(45deg);box-shadow:2px 2px 3px rgba(0,0,0,.08)}
.quote-mark{margin-top:22px;font-family:'Rubik',sans-serif;font-size:56px;line-height:40px;color:var(--brand);font-weight:600}
.quote-text{margin:8px 24px 0;font-size:12.5px;line-height:22.5px;font-style:italic;color:var(--muted)}
.author{position:absolute;top:2442px;display:flex;align-items:center;gap:12px}
.avatar{width:44px;height:44px;border-radius:50%;background:linear-gradient(135deg,#c9a88f,#6d7a86)}
.author b{display:block;font-size:15px;font-weight:700}
.author span{display:block;font-size:10px;font-weight:500}

/* services */
.service-card{position:absolute;top:2810px;width:215px;height:235px;display:flex;align-items:flex-end;justify-content:center;padding-bottom:28px;color:var(--white);font-weight:700;font-size:15px;line-height:20px;text-align:center}

/* footer */
.foot-links{position:absolute;top:3340px;font-size:11.5px;line-height:30px}
.foot-links a{display:block;color:#333;text-decoration:none}
.social{position:absolute;left:142px;top:3428px;display:flex;gap:26px}
.social span{width:16px;height:16px;border-radius:50%;background:var(--ink)}
.newsletter-field{position:absolute;left:737px;top:3384px;width:318px;height:46px;border:1px solid #cfd5da;border-radius:23px;display:flex;align-items:center;padding-left:22px;font-size:12px;color:var(--muted)}
.newsletter-field .send{position:absolute;right:3px;top:3px;width:104px;height:38px;border-radius:19px;background:var(--brand);color:var(--white);font-weight:700;font-size:15px;display:flex;align-items:center;justify-content:center}
.legal{position:absolute;top:3556px;font-size:11px;color:#555}
</style>
</head>
<body>

<!-- header -->
<header>
  <div class="brand-mark" style="left:142px;top:33px">
    <span class="brand-dot"></span>
    <span class="brand-name">Ledgerwise Forge</span>
  </div>
  <nav class="main-nav">
    <a class="active" href="#services">Services</a>
    <a href="#method">Ledgerwise Forge Method</a>
    <a href="#testimonials">Testimonials</a>
    <a href="#blog">Blog</a>
    <a href="#about">About Us</a>
  </nav>
  <a class="btn" href="#consult" style="left:866px;top:24px;width:190px;height:42px;font-size:13px">Schedule Free Consultation</a>
</header>

<!-- hero -->
<section>
  <div class="abs" role="img" aria-label="Faint hexagon pattern background" style="left:0;top:140px;width:1200px;height:320px;background:radial-gradient(ellipse at 15% 40%,#f1f2fb 0,transparent 30%),radial-gradient(ellipse at 85% 40%,#f1f2fb 0,transparent 30%)"></div>
  <h1 class="abs hero-title centered" style="top:150px">Your own cryptocurrency. Secure,<br>easy to use, and built by an expert team</h1>
  <p class="abs hero-text centered" style="top:276px">Ledgerwise Forge adds professionalism to cryptocurrency development. Our done-for-you service<br>covers everything from development and IT operations to ongoing support. You have access to<br>a full team, for less than the typical cost of a single developer.</p>
  <a class="btn" href="#consult" style="left:490px;top:383px;width:220px;height:50px">Schedule Free Consultation</a>
  <div class="abs" role="img" aria-label="Wave of blue dots forming a digital landscape" style="left:0;top:490px;width:1200px;height:270px;background:linear-gradient(180deg,rgba(255,255,255,0) 0,#e3f4fa 40%,#bfe6f4 70%,rgba(255,255,255,0) 100%)"></div>
  <div class="side-index" style="top:250px">Home</div>
</section>

<!-- why -->
<section>
  <h2 class="abs centered" style="top:860px;font-size:40px">Why choose Ledgerwise Forge</h2>
  <div class="rule" style="left:575px;top:927px"></div>
  <div class="side-index" style="top:868px">Why</div>

  <div class="hex-card" style="left:143px;top:1007px">
    <svg width="300" height="342" viewBox="0 0 300 342"><polygon points="150,3 296,87 296,255 150,339 4,255 4,87" fill="#fff" stroke="var(--brand)" stroke-width="2.5"/></svg>
    <svg class="icon" width="70" height="52" viewBox="0 0 70 52"><circle cx="35" cy="12" r="11" fill="var(--brand)"/><circle cx="13" cy="17" r="7" fill="var(--brand)"/><circle cx="57" cy="17" r="7" fill="var(--brand)"/><path d="M16 50c0-14 8-22 19-22s19 8 19 22z" fill="var(--brand)"/><path d="M1 44c0-10 5-16 12-16 3 0 5 1 7 2-3 4-5 9-5 14z" fill="var(--brand)"/><path d="M69 44c0-10-5-16-12-16-3 0-5 1-7 2 3 4 5 9 5 14z" fill="var(--brand)"/></svg>
    <div class="label">VALUE</div>
    <div class="desc">A team of experts, regular updates, and fixed costs</div>
  </div>

  <div class="hex-card featured" style="left:450px;top:1007px">
    <svg width="300" height="342" viewBox="0 0 300 342"><defs><linearGradient id="hexfill" x1="0" y1="0" x2="0" y2="1"><stop offset="0" stop-color="#a4e8fa"/><stop offset="1" stop-color="#16aedd"/></linearGradient></defs><polygon points="150,0 298,86 298,256 150,342 2,256 2,86" fill="url(#hexfill)"/></svg>
    <svg class="icon" width="70" height="56" viewBox="0 0 70 56"><path d="M10 40V30a25 25 0 0 1 50 0v10" fill="none" stroke="#fff" stroke-width="6"/><rect x="6" y="30" width="14" height="24" rx="4" fill="#fff"/><rect x="50" y="30" width="14" height="24" rx="4" fill="#fff"/></svg>
    <div class="label">SUPPORT</div>
    <div class="desc">Receive advice and other services, beyond development.</div>
  </div>

  <div class="hex-card" style="left:757px;top:1007px">
    <svg width="300" height="342" viewBox="0 0 300 342"><polygon points="150,3 296,87 296,255 150,339 4,255 4,87" fill="#fff" stroke="var(--brand)" stroke-width="2.5"/></svg>
    <svg class="icon" width="70" height="52" viewBox="0 0 70 52"><rect x="6" y="2" width="14" height="14" fill="var(--brand)"/><rect x="24" y="2" width="40" height="14" fill="var(--brand)"/><rect x="6" y="19" width="14" height="14" fill="var(--brand)"/><rect x="24" y="19" width="40" height="14" fill="var(--brand)"/><rect x="6" y="36" width="14" height="14" fill="var(--brand)"/><rect x="24" y="36" width="40" height="14" fill="var(--brand)"/></svg>
    <div class="label">COMMITMENT</div>
    <div class="desc">Enjoy regular updates and new features.</div>
  </div>
</section>

<!-- about -->
<section id="about">
  <svg class="abs" style="left:0;top:1430px" width="1200" height="600" viewBox="0 0 1200 600">
    <path d="M0 120C200 20 500 0 700 8C950 18 1120 70 1200 110V460C1050 560 800 590 600 585C350 580 120 520 0 470Z" fill="var(--band)"/>
    <path d="M0 120C160 40 420 8 640 6C500 20 200 60 0 160Z" fill="var(--band-edge)"/>
    <path d="M1200 420C1100 520 900 575 620 588C900 560 1080 500 1200 450Z" fill="var(--band-edge)"/>
  </svg>
  <h2 class="abs" style="left:189px;top:1565px;font-size:40px">Who we are</h2>
  <div class="rule" style="left:189px;top:1632px"></div>
  <p class="abs about-text" style="left:189px;top:1665px">In addition to creating and enhancing cryptocurrencies for clients, the Ledgerwise Forge team has been running the Corvel cryptocurrency since 2017. We prefer long-term relationships,enabling us to deliver the very highest quality and giving you peace of mind that you've got a professional and trustworthy team at your side</p>
  <a class="btn" href="#consult" style="left:189px;top:1840px;width:219px;height:50px">Schedule Free Consultation</a>
  <svg class="abs" style="left:604px;top:1526px" width="412" height="412" viewBox="0 0 412 412">
    <path d="M206 4A202 202 0 0 1 206 408" fill="none" stroke="var(--brand)" stroke-width="8"/>
    <path d="M206 4A202 202 0 0 0 40 90" fill="none" stroke="var(--brand)" stroke-width="8"/>
  </svg>
  <div class="abs" role="img" aria-label="Developer working on a laptop outdoors with a network diagram overlay" style="left:616px;top:1548px;width:378px;height:378px;border-radius:50%;background:radial-gradient(circle at 60% 40%,#8d9299,#4e545c 70%,#3a3f46)"></div>
  <div class="side-index" style="top:1695px">About</div>
</section>

<!-- testimonials -->
<section id="testimonials">
  <h2 class="abs centered" style="top:2110px;font-size:40px">Client Testimonials</h2>
  <div class="rule" style="left:575px;top:2178px"></div>
  <div class="side-index" style="top:2272px">Testimonials</div>

  <div class="quote-card" style="left:134px;width:302px"><div class="quote-mark">&ldquo;</div><p class="quote-text">In ullamcorper est eget tempor cursus neque mi consectetuer mi a ultricies massa est sed nisl Class aptent taciti sociosqu ad litora torquent per conubia nostra</p></div>
  <div class="quote-card" style="left:450px;width:305px"><div class="quote-mark">&ldquo;</div><p class="quote-text">In ullamcorper est eget tempor cursus neque mi consectetuer mi a ultricies massa est sed nisl Class aptent taciti sociosqu ad litora torquent per conubia nostra</p></div>
  <div class="quote-card" style="left:770px;width:296px"><div class="quote-mark">&ldquo;</div><p class="quote-text">In ullamcorper est eget tempor cursus neque mi consectetuer mi a ultricies massa est sed nisl Class aptent taciti sociosqu ad litora torquent per conubia nostra</p></div>

  <div class="author" style="left:210px"><span class="avatar" role="img" aria-label="Client portrait"></span><div><b>By Author Name</b><span>City, Location</span></div></div>
  <div class="author" style="left:523px"><span class="avatar" role="img" aria-label="Client portrait"></span><div><b>By Author Name</b><span>City, Location</span></div></div>
  <div class="author" style="left:847px"><span class="avatar" role="img" aria-label="Client portrait"></span><div><b>By Author Name</b><span>City, Location</span></div></div>
</section>

<!-- services -->
<section id="services">
  <svg class="abs" style="left:0;top:2595px" width="1200" height="670" viewBox="0 0 1200 670">
    <path d="M0 120C200 40 450 8 700 10C950 14 1120 60 1200 100V560C1050 640 800 668 600 666C330 662 120 610 0 560Z" fill="var(--band)"/>
    <path d="M0 120C150 50 380 14 600 8C420 30 180 80 0 145Z" fill="var(--band-edge)"/>
  </svg>
  <h2 class="abs centered" style="top:2697px;font-size:40px">Our Services</h2>
  <div class="rule" style="left:575px;top:2765px"></div>
  <div class="side-index" style="top:2898px">Services</div>

  <div class="service-card" role="img" aria-label="Glowing digital chain link" style="left:144px;background:linear-gradient(160deg,#23405a,#0c1620)">Blockchain Creation<br>&amp; Launch</div>
  <div class="service-card" role="img" aria-label="Hand typing with binary code overlay" style="left:376px;background:linear-gradient(160deg,#2c3e66,#0b1224)">Blockchain<br>Development</div>
  <div class="service-card" role="img" aria-label="Dark teal circuitry scene" style="left:608px;background:linear-gradient(160deg,#17403d,#071210)">Blockchain<br>Operations</div>
  <div class="service-card" role="img" aria-label="Person using a holographic blockchain dashboard" style="left:840px;background:linear-gradient(160deg,#3f5c86,#141a2a)">Blockchain<br>Support</div>

  <a class="btn" href="#consult" style="left:490px;top:3098px;width:220px;height:50px">Schedule Free Consultation</a>
</section>

<!-- footer -->
<footer>
  <div class="abs" role="img" aria-label="Faint hexagon and dot pattern" style="left:0;top:3290px;width:1200px;height:313px;background:radial-gradient(ellipse at 8% 50%,#f1f2fb 0,transparent 25%),radial-gradient(ellipse at 92% 20%,#f1f2fb 0,transparent 25%),linear-gradient(180deg,transparent 70%,#e6f5fa)"></div>
  <div class="brand-mark" style="left:142px;top:3360px">
    <span class="brand-dot"></span>
    <span class="brand-name">Ledgerwise Forge</span>
  </div>
  <div class="social" aria-label="Social links"><span></span><span></span><span></span><span></span><span></span></div>
  <nav class="foot-links" style="left:425px"><a href="#services">Services</a><a href="#method">Ledgerwise Forge</a><a href="#method">Method</a><a href="#testimonials">Testimonials</a></nav>
  <nav class="foot-links" style="left:600px"><a href="#blog">Blog</a><a href="#about">About Us</a><a href="#consult">Schedule Free</a><a href="#consult">Consultation</a></nav>
  <div class="abs" style="left:737px;top:3337px;font-family:'Rubik',sans-serif;font-weight:500;font-size:22px">Get Our Newsletter</div>
  <div class="newsletter-field"><span style="display:inline-block;width:14px;height:10px;border:1.5px solid var(--brand);margin-right:12px"></span>Email Address<span class="send">SEND</span></div>
  <div class="abs" style="left:0;top:3510px;width:1200px;height:1px;background:#e6e8ea"></div>
  <p class="legal centered">&copy; 2021, Ledgerwise Forge. All Rights Reserved &nbsp;|&nbsp; Privacy Policy &nbsp;|&nbsp; Terms and Use</p>
</footer>

</body>
</html>
```